Web design for sitter site

We will be launching a sitter site in the coming months that focuses on sitters for children. The name of this site will be NestWatch.com
We will need:
1. main page design
2. site logo designed
3. subpages as well for the look of people's profiles, and job listings, etc (see links below)
We only need the design, photos, font files, etc. We do not need this site coded (no html), a ps job is fine.
Some competing sites in the space include - tendlane.com and brio.com
http://www.pebble-keeper.example/images/profile1.jpg
http://marrowbooks.example/wp-content/uploads/2013/09/brio-review.png
http://www.quillmont.example/hr/photos/tend_lane2.jpg
Thanks for your interest!
Mothers of children, mainly women
Online

```html
<!DOCTYPE html>
<html lang="en">
<head>
<meta charset="utf-8">
<title>NestWatch — Sign up</title>
<link rel="stylesheet" href="https://fonts.googleapis.com/css2?family=Source+Sans+3:wght@400;600;700&display=swap">
<style>
  :root {
    --brand: #1489b6;
    --brand-deep: #0f77a2;
    --heading: #137fa7;
    --ink: #222;
    --body: #333;
    --footer: #1590bf;
    --footer-bar: #0e79a6;
    --field: #ffffff;
    --white: #ffffff;
  }
  * { box-sizing: border-box; margin: 0; padding: 0; }
  html, body { width: 1200px; height: 1200px; overflow: hidden; }
  body { font-family: "Source Sans 3", sans-serif; color: var(--body); background: var(--white); position: relative; }
  .abs { position: absolute; }
  h1, h2 { font-weight: 400; }

  .top-rule { left: 0; top: 0; width: 1200px; height: 5px; background: var(--brand); }
  .logo { left: 133px; top: 38px; font-size: 38px; font-weight: 400; color: var(--brand); line-height: 1; }
  .nav { left: 576px; top: 55px; font-size: 16px; color: var(--ink); display: flex; white-space: nowrap; }
  .nav .sep { margin: 0 17px; }
  .login { left: 985px; top: 47px; width: 86px; height: 37px; border-radius: 19px; background: var(--brand); color: var(--white); font-size: 16px; text-align: center; line-height: 37px; }

  .hero { left: 0; top: 113px; width: 1200px; height: 475px;
    background: linear-gradient(90deg, #d9eef9 0%, #c6e5f6 35%, #bfe1f3 55%, #b7dcee 80%, #cfe8d0 100%); }
  .hero-portrait { left: 640px; top: 113px; width: 450px; height: 475px;
    background: linear-gradient(180deg, #4a3630 0%, #b98572 45%, #d7a58e 70%, #b8505e 100%); }
  .hero-rule { left: 0; top: 588px; width: 1200px; height: 4px; background: var(--brand); }

  .hero-title { left: 157px; top: 176px; font-size: 41.5px; color: var(--heading); line-height: 1.2; }
  .field { background: var(--field); border-radius: 6px; font-size: 16px; color: var(--body); padding-left: 21px; line-height: 50px; height: 50px; }
  .field-email { left: 153px; top: 248px; width: 457px; }
  .field-pass { left: 153px; top: 310px; width: 227px; }
  .field-confirm { left: 385px; top: 310px; width: 227px; padding-left: 17px; }
  .field-zip { left: 153px; top: 372px; width: 457px; }
  .checkbox { left: 158px; top: 445px; width: 16px; height: 16px; background: var(--white); border-radius: 2px; }
  .terms { left: 182px; top: 440px; width: 430px; font-size: 14.5px; line-height: 24px; color: var(--ink); }
  .join { left: 252px; top: 504px; width: 174px; height: 48px; border-radius: 24px;
    background: linear-gradient(#22a3cf, #0f7fac); color: var(--white); font-size: 22px; text-align: center; line-height: 48px; }
  .slider-dot { left: 1111px; width: 15px; height: 15px; border-radius: 50%; background: var(--white); }
  .slider-dot.active { background: var(--brand); }

  .section-title { left: 0; top: 606px; width: 1200px; text-align: center; font-size: 41px; color: var(--heading); line-height: 1.2; }
  .card-photo { top: 679px; width: 311px; height: 151px; border-radius: 6px; }
  .card-text { top: 842px; width: 312px; font-size: 14.5px; line-height: 24px; color: var(--body); }
  .card-btn { top: 901px; width: 101px; height: 31px; border-radius: 16px; background: var(--brand); color: var(--white); font-size: 16px; text-align: center; line-height: 31px; }

  .footer { left: 0; top: 966px; width: 1200px; height: 194px; background: var(--footer); }
  .footer-bar { left: 0; top: 1160px; width: 1200px; height: 40px; background: var(--footer-bar); }
  .footer-links { top: 988px; list-style: none; font-size: 13.5px; line-height: 24px; color: var(--white); }
  .footer-about { left: 412px; top: 993px; width: 200px; font-size: 13.5px; line-height: 18px; color: var(--white); }
  .footer-about strong { font-weight: 700; margin-right: 6px; }
  .footer-address { left: 660px; top: 988px; font-size: 13.5px; line-height: 24px; color: var(--white); }
  .social { top: 995px; width: 38px; height: 38px; border-radius: 6px; }
  .copyright { left: 0; top: 1172px; width: 1172px; text-align: center; font-size: 12.5px; color: var(--white); }
</style>
</head>
<body>
  <div class="abs top-rule"></div>
  <div class="abs logo">NestWatch</div>
  <nav class="abs nav">
    <span>Trust &amp; Safty Center</span><span class="sep">::</span>
    <span>Sign Up Parents</span><span class="sep">::</span>
    <span>Sitters</span>
  </nav>
  <div class="abs login">Login</div>

  <div class="abs hero" role="img" aria-label="Soft blurred meadow of green grass against a pale blue sky"></div>
  <div class="abs hero-portrait" role="img" aria-label="Portrait photo of a smiling young woman with dark bobbed hair"></div>
  <div class="abs hero-rule"></div>

  <h1 class="abs hero-title">Sign up to start your FREE</h1>
  <div class="abs field field-email">Email Address</div>
  <div class="abs field field-pass">Password</div>
  <div class="abs field field-confirm">Confirm Password</div>
  <div class="abs field field-zip">Zip Code</div>
  <div class="abs checkbox"></div>
  <p class="abs terms">I agree to the Terms of Use. For details on collection and use of your information, see our Privacy Policy.</p>
  <div class="abs join">Join Now</div>
  <div class="abs slider-dot active" style="top:485px"></div>
  <div class="abs slider-dot" style="top:507px"></div>
  <div class="abs slider-dot" style="top:529px"></div>
  <div class="abs slider-dot" style="top:551px"></div>

  <h2 class="abs section-title">Introducing the best way to pay for care</h2>

  <div class="abs card-photo" style="left:117px;background:linear-gradient(135deg,#c98a6c,#f0d2b8 55%,#e9e1d6)" role="img" aria-label="Photo of a woman helping a small child draw"></div>
  <p class="abs card-text" style="left:119px">Duis aute irure dolor in reprehenderit in voluptate velit esse cillum dolore eu fugiat nulla pariatur.</p>
  <div class="abs card-btn" style="left:117px">Get Started</div>

  <div class="abs card-photo" style="left:444px;background:linear-gradient(90deg,#e8e8ea,#6fa8cf 35%,#b49a82 60%,#26a6b8)" role="img" aria-label="Photo of a caregiver sitting with an elderly woman"></div>
  <p class="abs card-text" style="left:450px">Duis aute irure dolor in reprehenderit in voluptate velit esse cillum dolore eu fugiat nulla pariatur.</p>
  <div class="abs card-btn" style="left:449px">Get Started</div>

  <div class="abs card-photo" style="left:770px;background:linear-gradient(90deg,#5f9a3a,#e8c9a8 35%,#d9a25c 70%,#6aa53f)" role="img" aria-label="Photo of a smiling woman hugging a golden retriever on grass"></div>
  <p class="abs card-text" style="left:773px">Duis aute irure dolor in reprehenderit in voluptate velit esse cillum dolore eu fugiat nulla pariatur.</p>
  <div class="abs card-btn" style="left:770px">Get Started</div>

  <footer>
    <div class="abs footer"></div>
    <ul class="abs footer-links" style="left:123px">
      <li>Home</li><li>About Us</li><li>Services</li><li>Testimonials</li><li>Contact</li><li>Blog</li>
    </ul>
    <ul class="abs footer-links" style="left:283px">
      <li>Home</li><li>About Us</li><li>Services</li><li>Testimonials</li><li>Contact</li><li>Blog</li>
    </ul>
    <p class="abs footer-about"><strong>About Us</strong> unde omnis iste natus error sit voluptatem accusantium doloremque laudantium, totam rem aperiam, eaque ipsa quae ab illo inventore</p>
    <p class="abs footer-address">Address : xy/4 Lorium iopsum<br>sit amet, consecletur,<br>porta posuere.<br>Phone Number :&nbsp; + 60 312 4470 58</p>
    <div class="abs social" style="left:907px;background:#3b5a9a"></div>
    <div class="abs social" style="left:957px;background:#2aa6dc"></div>
    <div class="abs social" style="left:1007px;background:#d23a2c"></div>
    <div class="abs footer-bar"></div>
    <p class="abs copyright">© 2014.www.companyname.com</p>
  </footer>
</body>
</html>
```